Technical Communications firm needs an article turned into a white paper

We want to redesign a 3-part blog series into a white paper that we can print for a conference. I've consolidated the three posts into the attached Word document.

We are looking for a light, easy to read design. Good use of graphics to support the message. I've added the graphics we used in the original post.

You can view them at
http://www.brightquillpages.com/blog/are-you-satisfied-with-your-dita-solution/

Target Market(s)

Product managers from High-tech, Finance, and Medical industries.

Industry/Entity Type

Information Technology

Colors

Designer to choose colors to be used in the design.

Requirements
Must have
• Must be modern, light, easy to read and slick design. Try to incorporate the graphics provided, but feel free to add more. Must retain the lists and tables.
• Must align with our website/brand.
• Must be easy to read. So not too busy.
• Please move all footnotes to endnotes. You'll need to rework the numbering.
Nice to have
• Awesome coverpage.
Should not have
• Hokey clipart. Not too heavy or hard to read.

```html
<!DOCTYPE html>
<html lang="en">
<head>
<meta charset="utf-8">
<title>Are You Satisfied With Your Data Solution? – Page 2</title>
<link rel="stylesheet" href="https://fonts.googleapis.com/css2?family=Carlito:wght@400;700&family=Open+Sans:wght@700;800&display=swap">
<style>
  :root {
    --navy: #1c1c96;
    --cyan: #19a9e0;
    --ink: #333338;
    --paper: #ffffff;
    --slate-light: #66767c;
    --slate-dark: #46545a;
  }
  * { margin: 0; padding: 0; box-sizing: border-box; }
  html, body { width: 927px; height: 1200px; overflow: hidden; background: var(--paper); }
  .page {
    position: relative;
    width: 927px;
    height: 1200px;
    background: var(--paper);
    font-family: "Carlito", "Calibri", sans-serif;
    color: var(--ink);
  }

  /* Brand block */
  .brand { position: absolute; left: 85px; top: 57px; display: flex; align-items: center; gap: 8px; }
  .brand-mark { width: 86px; height: 86px; border-radius: 50%; background: var(--navy); }
  .brand-name {
    font-family: "Open Sans", sans-serif;
    font-weight: 800;
    color: var(--navy);
    font-size: 23px;
    line-height: 22px;
    letter-spacing: -0.2px;
  }

  .margin-rule { position: absolute; left: 112px; top: 142px; width: 3px; height: 924px; background: var(--navy); }

  .page-label {
    position: absolute; left: 750px; top: 71px; width: 125px; height: 28px;
    border-top: 1px solid var(--cyan); border-bottom: 1px solid var(--cyan);
    font-family: "Open Sans", sans-serif; font-weight: 700; font-size: 14px;
    color: var(--navy); letter-spacing: 1.5px;
    display: flex; align-items: center; padding-left: 30px;
  }

  .article-title {
    position: absolute; left: 180px; top: 152px; width: 695px;
    font-family: "Open Sans", sans-serif; font-weight: 700;
    font-size: 34.5px; line-height: 44px; color: var(--navy);
    text-decoration: underline; text-decoration-thickness: 2px; text-underline-offset: 5px;
    letter-spacing: -0.4px; white-space: nowrap;
  }

  .hero-photo {
    position: absolute; left: 180px; top: 210px; width: 695px; height: 292px;
    background: linear-gradient(100deg, var(--slate-light) 0%, var(--slate-dark) 100%);
  }

  .body-copy {
    position: absolute; left: 175px; width: 699px;
    font-size: 15.6px; line-height: 22.8px; text-align: justify;
  }
  .body-copy.indent { text-indent: 28px; }
  .intro-para { top: 530px; }
  .followup-para { top: 690px; }
  .issues-intro { top: 798px; }
  .issues-summary { top: 918px; }

  .section-heading {
    position: absolute; left: 175px; top: 752px; width: 699px; text-align: center;
    font-family: "Open Sans", sans-serif; font-weight: 700; font-size: 30px; line-height: 40px;
    color: var(--navy);
    text-decoration: underline; text-decoration-thickness: 2px; text-underline-offset: 5px;
  }

  .issue-list { position: absolute; left: 258px; top: 845px; list-style: none; font-size: 15.6px; line-height: 24.4px; }
  .issue-list li { position: relative; padding-left: 27px; }
  .issue-list li::before {
    content: ""; position: absolute; left: 0; top: 10px;
    width: 6px; height: 6px; border-radius: 50%; background: var(--navy);
  }

  .dot-rule { position: absolute; left: 106px; top: 1077px; }
</style>
</head>
<body>
<main class="page">
  <header>
    <div class="brand">
      <span class="brand-mark" aria-hidden="true"></span>
      <span class="brand-name">BRIGHTQUILL<br>PAGES</span>
    </div>
    <div class="page-label">PAGE 2</div>
  </header>

  <div class="margin-rule" aria-hidden="true"></div>

  <h1 class="article-title">Are You Satisfied With Your Data Solution?</h1>

  <div class="hero-photo" role="img" aria-label="Photo of a bearded man looking up at chalk star ratings on a blackboard, with the one-star box ticked"></div>

  <p class="body-copy indent intro-para">If your answer is “No” then you are not alone according to a 2017 survey of more than 250 technical communication professionals conducted by The Content Corral. The DITA Satisfaction Survey [1] indicates that 62% of respondents using DITA are — to varying degrees — dissatisfied. As many as 10% of that group were very dissatisfied, reporting that their DITA implementation is experiencing ‘big’ challenges. It’s not surprising that there’s significant dissatisfaction amongst those who have adopted DITA. After all, moving to DITA is a seismic shift in technical writing; a big change with many opportunities for things to go wrong.</p>

  <p class="body-copy indent followup-para">The good news is that most DITA users don’t see their problems as insurmountable. Many just need a little help getting to where they’d ike to be.</p>

  <h2 class="section-heading">Breakdown of the Issues</h2>

  <p class="body-copy issues-intro">The Content Corral DITA Satisfaction Survey asked respondents to rank the top 10 issues facing DITA users. These issues fit into three major categories including</p>

  <ul class="issue-list">
    <li>skills development;</li>
    <li>technology; and</li>
    <li>management.</li>
  </ul>

  <p class="body-copy issues-summary">The DITA Satisfaction Survey Aggregate Results revealed little spread between the ranking of the issues indicating that respondents likely faced more than one issue of concern.</p>

  <svg class="dot-rule" width="770" height="14" viewBox="0 0 770 14" aria-hidden="true">
    <g>
      <circle cx="7" cy="7" r="6.5" fill="var(--navy)"/><circle cx="30" cy="7" r="6.5" fill="var(--cyan)"/>
      <circle cx="53" cy="7" r="6.5" fill="var(--navy)"/><circle cx="76" cy="7" r="6.5" fill="var(--cyan)"/>
      <circle cx="99" cy="7" r="6.5" fill="var(--navy)"/><circle cx="122" cy="7" r="6.5" fill="var(--cyan)"/>
      <circle cx="145" cy="7" r="6.5" fill="var(--navy)"/><circle cx="168" cy="7" r="6.5" fill="var(--cyan)"/>
      <circle cx="191" cy="7" r="6.5" fill="var(--navy)"/><circle cx="214" cy="7" r="6.5" fill="var(--cyan)"/>
      <circle cx="237" cy="7" r="6.5" fill="var(--navy)"/><circle cx="260" cy="7" r="6.5" fill="var(--cyan)"/>
      <circle cx="283" cy="7" r="6.5" fill="var(--navy)"/><circle cx="306" cy="7" r="6.5" fill="var(--cyan)"/>
      <circle cx="329" cy="7" r="6.5" fill="var(--navy)"/><circle cx="352" cy="7" r="6.5" fill="var(--cyan)"/>
      <circle cx="375" cy="7" r="6.5" fill="var(--navy)"/><circle cx="398" cy="7" r="6.5" fill="var(--cyan)"/>
      <circle cx="421" cy="7" r="6.5" fill="var(--navy)"/><circle cx="444" cy="7" r="6.5" fill="var(--cyan)"/>
      <circle cx="467" cy="7" r="6.5" fill="var(--navy)"/><circle cx="490" cy="7" r="6.5" fill="var(--cyan)"/>
      <circle cx="513" cy="7" r="6.5" fill="var(--navy)"/><circle cx="536" cy="7" r="6.5" fill="var(--cyan)"/>
      <circle cx="559" cy="7" r="6.5" fill="var(--navy)"/><circle cx="582" cy="7" r="6.5" fill="var(--cyan)"/>
      <circle cx="605" cy="7" r="6.5" fill="var(--navy)"/><circle cx="628" cy="7" r="6.5" fill="var(--cyan)"/>
      <circle cx="651" cy="7" r="6.5" fill="var(--navy)"/><circle cx="674" cy="7" r="6.5" fill="var(--cyan)"/>
      <circle cx="697" cy="7" r="6.5" fill="var(--navy)"/><circle cx="720" cy="7" r="6.5" fill="var(--cyan)"/>
      <circle cx="743" cy="7" r="6.5" fill="var(--navy)"/><circle cx="763" cy="7" r="6.5" fill="var(--cyan)"/>
    </g>
  </svg>
</main>
</body>
</html>
```